New Innovative Counselling and psychotherapy Service needs Business Card design

Keep it simple and professional. On one side, just company name and logo (perhaps in all blue) and maybe a tag line.

On other side (all white) my name and Qualifications in centre

Industry/Entity Type

Health And Wellness

Contact Information for Business Card

Dara Whelby
Counsellor & Psychotherapist
BSc (Psychol.), BA, Dip. (Couns. & Psych.), PG.Cert (CBT), FGTrK, ONRE

I will also require Mobile no, Email and web site address of which I'll pass on to final designer.

Font styles to use
Sans Serif

Requirements
Must have
• My Logo Only and please use the colours in logo that is in it.
Should not have
• Any other images

```html
<!DOCTYPE html>
<html lang="en">
<head>
<meta charset="utf-8">
<title>HaldenLane Business Card</title>
<link rel="stylesheet" href="https://fonts.googleapis.com/css2?family=Montserrat:wght@400;500;600&display=swap">
<style>
  :root {
    --backdrop: #3a332f;
    --card: #141414;
    --card-edge: #1d1d1d;
    --deboss: #262626;
    --text-light: #e8e8e8;
    --text-muted: #bdbdbd;
    --brand-blue: #3fa9e0;
    --brand-green: #7dc242;
  }
  * { margin: 0; padding: 0; box-sizing: border-box; }
  html, body { width: 1200px; height: 715px; overflow: hidden; }
  body {
    background: var(--backdrop);
    font-family: "Montserrat", sans-serif;
    position: relative;
  }
  .card {
    position: absolute;
    top: 203px;
    width: 540px;
    height: 309px;
    background: var(--card);
    border: 1px solid var(--card-edge);
    border-radius: 4px;
  }
  .card--front { left: 40px; }
  .card--back { left: 620px; }

  /* Front side */
  .front-mark {
    position: absolute;
    inset: 0;
    display: flex;
    align-items: center;
    justify-content: center;
    gap: 14px;
  }
  .front-mark__dot {
    width: 46px; height: 46px;
    border-radius: 50%;
    background: var(--deboss);
  }
  .front-mark__name {
    font-size: 30px;
    font-weight: 400;
    color: #3a3a3a;
    letter-spacing: 0.5px;
  }

  /* Back side */
  .brand {
    position: absolute;
    left: 34px;
    top: 118px;
    display: flex;
    align-items: center;
    gap: 10px;
  }
  .brand__dot {
    width: 26px; height: 26px;
    border-radius: 50%;
    background: var(--brand-blue);
  }
  .brand__name {
    font-size: 21px;
    font-weight: 400;
    color: var(--text-muted);
  }
  .divider {
    position: absolute;
    left: 282px;
    top: 108px;
    width: 2px;
    height: 150px;
    background: var(--brand-green);
  }
  .details {
    position: absolute;
    left: 298px;
    top: 104px;
    right: 16px;
    color: var(--text-light);
  }
  .details__name {
    font-size: 23px;
    font-weight: 600;
    color: var(--brand-blue);
    letter-spacing: 0.3px;
    line-height: 1.1;
    text-transform: uppercase;
  }
  .details__role,
  .details__quals {
    font-size: 11.5px;
    font-weight: 500;
    line-height: 1.35;
  }
  .details__role { margin-top: 3px; }
  .contact {
    list-style: none;
    margin-top: 12px;
  }
  .contact__item {
    display: flex;
    align-items: center;
    gap: 7px;
    font-size: 11.5px;
    line-height: 1.6;
  }
  .contact__icon { width: 9px; height: 9px; flex: none; }
  .contact__accent { color: var(--brand-green); }
</style>
</head>
<body>
  <section class="card card--front" aria-label="Card front">
    <div class="front-mark">
      <span class="front-mark__dot"></span>
      <span class="front-mark__name">HaldenLane</span>
    </div>
  </section>

  <section class="card card--back" aria-label="Card back">
    <div class="brand">
      <span class="brand__dot"></span>
      <span class="brand__name">HaldenLane</span>
    </div>
    <div class="divider"></div>
    <div class="details">
      <h1 class="details__name">Dara Whelby</h1>
      <p class="details__role">Counsellor &amp; Psychotherapist</p>
      <p class="details__quals">BSc (Psychol.), BA, Dip.<br>(Couns. &amp; Psych.), PG.Cert<br>(CBT), FGTrK, ONRE</p>
      <ul class="contact">
        <li class="contact__item">
          <svg class="contact__icon" viewBox="0 0 10 10" aria-hidden="true"><path d="M2 0.5 L4 2.6 L3 3.8 Q4.2 6 6.2 7 L7.4 6 L9.5 8 L8 9.5 Q3.5 9 0.5 2 Z" fill="var(--brand-blue)"/></svg>
          555-014-2738
        </li>
        <li class="contact__item">
          <svg class="contact__icon" viewBox="0 0 10 10" aria-hidden="true"><rect x="0.6" y="2" width="8.8" height="6.2" fill="none" stroke="var(--brand-blue)" stroke-width="1.2"/><path d="M0.6 2 L5 5.6 L9.4 2" fill="none" stroke="var(--brand-blue)" stroke-width="1.2"/></svg>
          info@haldenlane.com
        </li>
        <li class="contact__item">
          <svg class="contact__icon" viewBox="0 0 10 10" aria-hidden="true"><circle cx="5" cy="5" r="4.3" fill="none" stroke="var(--brand-blue)" stroke-width="1"/><ellipse cx="5" cy="5" rx="1.8" ry="4.3" fill="none" stroke="var(--brand-blue)" stroke-width="0.8"/><path d="M0.7 5 H9.3" stroke="var(--brand-blue)" stroke-width="0.8"/></svg>
          <span>www.<span class="contact__accent">haldenlane</span>.com</span>
        </li>
      </ul>
    </div>
  </section>
</body>
</html>
```